Sleek wordpress site for Bramblecrest finishing works

We are a commercial job shop that serves B2B, govt & LEO and retail clients.We need a wordpress site with 6 individual pages: homepage, coating, laser engraving, laser cutting, part marking, and contact us. I have attached an outline of the desired flow and sub headings for each page. I would like to incorporate the colors of the logo through out the site to be clean and sleek enough to appeal to B2B commercial clients yet be inviting enough for retail clients.

I would like to have easy picture functionality so photographs on each page can be updated easily.

Target Market(s)

B2B industrial & Govt and Military part marking, laser engraving and coating: machine shops, aerospace companies, tool manufactures. Retail: personalized gifts, Job Shop

Coding

Coded - Design and coding required

Font styles to use
Sans Serif
Other font styles liked:
• Open to suggestion

Colors
0255a3
3176b5
eaf1f7
cfdeed
ffffff

Requirements
Must have
• Clean easy to navigate flow, separate pages as indicated on attached outline, high class feel. Great picture functionality, professional and inviting feel,
• **update: needs to be optimized for mobile, should have a gallery function. Gallery can be an additional page or embedded
Nice to have
• Social media connectivity links,
Should not have
• crappy plugins that make back-end management difficult, no blog

```html
<!DOCTYPE html>
<html lang="en">
<head>
<meta charset="utf-8">
<title>Bramblecrest Finishing Works</title>
<link href="https://fonts.googleapis.com/css2?family=Lato:wght@400;700;900&display=swap" rel="stylesheet">
<style>
  :root{
    --brand:#0255a3;
    --brand-mid:#3176b5;
    --brand-deep:#0d3a78;
    --pale:#eaf1f7;
    --mist:#cfdeed;
    --white:#ffffff;
    --ink:#1b1b1b;
    --muted:#6b6b6b;
    --field:#e6e6e6;
    --field-line:#c9c9c9;
  }
  *{box-sizing:border-box;margin:0;padding:0}
  html,body{width:704px;height:1200px;overflow:hidden;background:var(--white)}
  body{font-family:'Lato',Arial,sans-serif;color:var(--ink);position:relative}
  .abs{position:absolute}

  /* header */
  .site-header{left:0;top:0;width:704px;height:54px;background:linear-gradient(#ffffff,#e9e9e9);z-index:5;box-shadow:0 1px 2px rgba(0,0,0,.15)}
  .brand-box{left:106px;top:0;width:137px;height:81px;background:var(--white);box-shadow:0 1px 4px rgba(0,0,0,.3);z-index:6;display:flex;align-items:center;justify-content:center;flex-direction:column;gap:5px}
  .brand-mark{width:16px;height:16px;border-radius:50%;background:var(--brand)}
  .brand-name{font-weight:900;font-size:10px;line-height:1.15;color:var(--brand);text-align:center;text-transform:uppercase}
  .header-phone{left:530px;top:11px;font-size:9.5px;color:#333;display:flex;align-items:center;gap:3px}
  .main-nav{left:262px;top:34px;display:flex;gap:13px;font-size:7.4px;color:#333;text-transform:uppercase}
  .main-nav .active{color:var(--brand)}

  /* hero */
  .hero{left:0;top:54px;width:704px;height:344px;
    background:
      radial-gradient(ellipse 60px 90px at 560px 60px,rgba(190,80,40,.45),rgba(190,80,40,0) 70%),
      radial-gradient(ellipse 70px 150px at 470px 90px,rgba(10,16,28,.9),rgba(10,16,28,0) 75%),
      radial-gradient(ellipse 260px 120px at 300px 250px,rgba(150,175,210,.35),rgba(150,175,210,0) 70%),
      radial-gradient(ellipse 220px 140px at 620px 180px,rgba(120,150,195,.4),rgba(120,150,195,0) 70%),
      radial-gradient(ellipse 300px 160px at 120px 120px,rgba(60,90,140,.5),rgba(60,90,140,0) 70%),
      linear-gradient(170deg,#2a4674 0%,#1d3358 45%,#243a5e 70%,#3a4a62 100%)}
  .hero-shade{left:0;top:54px;width:704px;height:344px;background:linear-gradient(90deg,rgba(8,18,36,.55) 0%,rgba(8,18,36,.15) 55%,rgba(8,18,36,0) 100%)}
  .hero-title{left:106px;top:154px;font-size:22px;font-weight:700;line-height:1.12;color:var(--white);text-transform:uppercase}
  .hero-text{left:106px;top:210px;width:220px;font-size:9.3px;line-height:1.35;color:var(--white)}
  .btn{display:flex;align-items:center;justify-content:center;font-size:8px;font-weight:700;text-transform:uppercase;text-decoration:none}
  .hero-btn{left:106px;top:246px;width:83px;height:23px;background:var(--brand);color:var(--white)}
  .slider-dots{left:329px;top:348px;display:flex;align-items:center;gap:3px}
  .slider-dots .dot{width:4px;height:4px;border-radius:50%;background:rgba(255,255,255,.5)}
  .slider-dots .dot.on{background:var(--white)}
  .hero-wave{left:0;top:350px}

  /* service cards */
  .card{width:119px;height:173px;top:398px}
  .card-photo{position:absolute;left:0;top:0;width:119px;height:116px;clip-path:polygon(0 0,86% 0,100% 12%,100% 100%,0 100%)}
  .card-photo::after{content:"";position:absolute;inset:0;background:linear-gradient(rgba(0,0,0,0) 55%,rgba(0,0,0,.45) 100%)}
  .card-label{position:absolute;left:10px;top:90px;font-size:8.5px;color:var(--white);text-transform:uppercase;z-index:2}
  .card-rule{position:absolute;left:0;top:103px;width:106px;height:1px;background:var(--white);z-index:2}
  .card-rule::after{content:"";position:absolute;right:-1px;top:-2px;width:4px;height:4px;border-radius:50%;background:var(--white)}
  .card-body{position:absolute;left:0;top:116px;width:119px;height:57px;border:1px solid var(--brand);border-top:none;padding:8px 9px 0}
  .card-body p{font-size:5.9px;line-height:1.4;color:var(--muted)}
  .card-body a{display:block;margin-top:3px;font-size:6.3px;font-weight:700;color:var(--brand);text-decoration:none;text-transform:uppercase}

  /* about */
  .about-band{left:0;top:584px}
  .about-title{left:113px;top:664px;font-size:15.5px;font-weight:700;line-height:1.25;color:var(--white);text-transform:uppercase}
  .about-text{left:113px;top:709px;width:228px;font-size:7.2px;line-height:1.45;color:var(--white)}
  .about-btn{left:113px;top:774px;width:79px;height:22px;background:var(--mist);color:var(--brand)}

  /* contact */
  .contact-title{left:106px;top:936px;font-size:14.5px;font-weight:900;color:#111;text-transform:uppercase}
  .contact-line{left:106px;display:flex;align-items:center;gap:7px;font-size:9.5px;font-weight:700;color:var(--brand);line-height:1.4}
  .field{background:var(--field);border:1px solid var(--field-line);font-size:6.6px;color:#777;padding:0 9px;display:flex;align-items:center;text-transform:uppercase}
  .field.area{align-items:flex-start;padding-top:8px}
  .submit-btn{left:272px;top:1058px;width:79px;height:22px;background:var(--brand);color:var(--white);font-size:9px}

  /* footer */
  .site-footer{left:0;top:1126px;width:704px;height:74px;background:linear-gradient(#eeeeee,#f6f6f6)}
  .footer-nav{left:112px;top:1150px;display:flex;gap:13px;font-size:7.4px;color:#333;text-transform:uppercase}
  .copyright{left:112px;top:1169px;font-size:6.8px;color:#555}
  .social{left:512px;top:1145px;display:flex;gap:3px}
  .social span{width:18px;height:18px;border-radius:50%;border:1px solid #8a8a8a;background:radial-gradient(circle,#ffffff 0%,#f1f1f1 100%);box-shadow:inset 0 0 0 3px #f6f6f6,inset 0 0 0 4px #d4d4d4}
</style>
</head>
<body>

<header class="abs site-header">
  <div class="abs header-phone">
    <svg width="10" height="10" viewBox="0 0 24 24"><path fill="#0255a3" d="M6.6 10.8a15 15 0 0 0 6.6 6.6l2.2-2.2a1 1 0 0 1 1-.25 11.4 11.4 0 0 0 3.6.57 1 1 0 0 1 1 1V20a1 1 0 0 1-1 1A17 17 0 0 1 3 4a1 1 0 0 1 1-1h3.5a1 1 0 0 1 1 1c0 1.25.2 2.45.57 3.57a1 1 0 0 1-.25 1z"/></svg>
    (555) 214-0388
  </div>
  <nav class="abs main-nav">
    <span class="active">Home</span><span>Coating</span><span>Laser Engraving</span><span>Laser Cutting</span><span>Part Marking</span><span>Contact Us</span>
  </nav>
</header>

<div class="abs brand-box">
  <span class="brand-mark"></span>
  <span class="brand-name">Bramblecrest<br>finishing works</span>
</div>

<section class="abs hero" role="img" aria-label="Photo of a laser head engraving a metal plate through drifting smoke"></section>
<div class="abs hero-shade"></div>
<h1 class="abs hero-title">Laser engraving<br>and cutting</h1>
<p class="abs hero-text">Ceraflex is a spray on ceramic based finish that can be applied to metals, plastics, polymers and wood.</p>
<a class="abs btn hero-btn">Read more</a>
<div class="abs slider-dots">
  <svg width="8" height="8" viewBox="0 0 8 8"><circle cx="4" cy="4" r="4" fill="#fff"/><path d="M4.6 2.2 2.8 4l1.8 1.8" stroke="#1d3358" stroke-width="1" fill="none"/></svg>
  <span class="dot on"></span><span class="dot"></span><span class="dot"></span><span class="dot"></span>
  <svg width="8" height="8" viewBox="0 0 8 8"><circle cx="4" cy="4" r="4" fill="#fff"/><path d="M3.4 2.2 5.2 4 3.4 5.8" stroke="#1d3358" stroke-width="1" fill="none"/></svg>
</div>

<svg class="abs hero-wave" width="704" height="56" viewBox="0 0 704 56">
  <polygon points="0,6 704,12 704,56 0,56" fill="#ffffff"/>
  <polygon points="0,6 90,14 360,18 704,12 704,24 380,22 0,42" fill="#0d3a78"/>
  <polygon points="0,22 220,16 400,18 704,28 704,40 560,24 300,20 0,30" fill="#3176b5"/>
  <polygon points="560,24 704,34 704,52" fill="#cfdeed"/>
  <path d="M0,42 C200,24 420,18 704,22 L704,24 C430,22 220,30 0,50 Z" fill="#ffffff"/>
</svg>

<article class="abs card" style="left:109px">
  <div class="card-photo" role="img" aria-label="Photo of laser engraved metal coins" style="background:radial-gradient(ellipse 50px 25px at 60px 70px,rgba(190,120,80,.7),rgba(190,120,80,0) 80%),radial-gradient(ellipse 30px 40px at 70px 20px,rgba(110,120,135,.8),rgba(110,120,135,0) 80%),linear-gradient(170deg,#3d4656 0%,#5b4a42 50%,#6e4b38 70%,#2b2420 100%)"></div>
  <span class="card-label">Laser engraving</span><span class="card-rule"></span>
  <div class="card-body"><p>Lorem ipsum dolor sit amet consec tetuer adipiscing elit Nam cursus ut mi Nullam enim leo egestas</p><a>Read more</a></div>
</article>
<article class="abs card" style="left:230px">
  <div class="card-photo" role="img" aria-label="Photo of a laser cutter slicing a red sheet" style="background:radial-gradient(ellipse 45px 20px at 60px 70px,rgba(235,70,80,.85),rgba(235,70,80,0) 80%),radial-gradient(ellipse 20px 50px at 62px 30px,rgba(220,220,225,.6),rgba(220,220,225,0) 80%),linear-gradient(170deg,#4a505a 0%,#5d3a44 45%,#8e2432 70%,#2a1a1e 100%)"></div>
  <span class="card-label">Laser cutting</span><span class="card-rule"></span>
  <div class="card-body"><p>Lorem ipsum dolor sit amet consec tetuer adipiscing elit Nam cursus ut mi Nullam enim leo egestas</p><a>Read more</a></div>
</article>
<article class="abs card" style="left:353px">
  <div class="card-photo" role="img" aria-label="Photo of a machine marking a metal part" style="background:radial-gradient(ellipse 40px 30px at 40px 70px,rgba(190,205,220,.6),rgba(190,205,220,0) 80%),radial-gradient(ellipse 25px 45px at 70px 25px,rgba(140,160,185,.6),rgba(140,160,185,0) 80%),linear-gradient(170deg,#7488a0 0%,#3c5474 45%,#253a58 70%,#121e32 100%)"></div>
  <span class="card-label">Part marking</span><span class="card-rule"></span>
  <div class="card-body"><p>Lorem ipsum dolor sit amet consec tetuer adipiscing elit Nam cursus ut mi Nullam enim leo egestas</p><a>Read more</a></div>
</article>
<article class="abs card" style="left:475px">
  <div class="card-photo" role="img" aria-label="Photo of a technician spray coating parts" style="background:radial-gradient(ellipse 25px 45px at 105px 50px,rgba(170,200,80,.6),rgba(170,200,80,0) 80%),radial-gradient(ellipse 30px 60px at 40px 55px,rgba(240,240,242,.8),rgba(240,240,242,0) 80%),linear-gradient(170deg,#d4d7db 0%,#a8adb4 45%,#7d858f 70%,#4c5660 100%)"></div>
  <span class="card-label">Coatings</span><span class="card-rule"></span>
  <div class="card-body"><p>Lorem ipsum dolor sit amet consec tetuer adipiscing elit Nam cursus ut mi Nullam enim leo egestas</p><a>Read more</a></div>
</article>

<svg class="abs about-band" width="704" height="320" viewBox="0 0 704 320" role="img" aria-label="Photo of a laser cutting head throwing sparks over sheet metal">
  <defs>
    <linearGradient id="aboutFade" x1="0" x2="1" y1="0" y2="0">
      <stop offset="0" stop-color="#245fae"/>
      <stop offset="0.42" stop-color="#1f5aa6"/>
      <stop offset="0.62" stop-color="#1d4274"/>
      <stop offset="0.8" stop-color="#15294a"/>
      <stop offset="1" stop-color="#0c1a30"/>
    </linearGradient>
    <radialGradient id="spark" cx="0.74" cy="0.46" r="0.16">
      <stop offset="0" stop-color="#fbe6a0" stop-opacity=".9"/>
      <stop offset="0.35" stop-color="#e8b85c" stop-opacity=".45"/>
      <stop offset="1" stop-color="#e8b85c" stop-opacity="0"/>
    </radialGradient>
    <radialGradient id="steel" cx="0.75" cy="0.15" r="0.22">
      <stop offset="0" stop-color="#6d7f98" stop-opacity=".55"/>
      <stop offset="1" stop-color="#6d7f98" stop-opacity="0"/>
    </radialGradient>
    <radialGradient id="sheet" cx="0.78" cy="0.75" r="0.3">
      <stop offset="0" stop-color="#3a5680" stop-opacity=".5"/>
      <stop offset="1" stop-color="#3a5680" stop-opacity="0"/>
    </radialGradient>
  </defs>
  <polygon points="0,16 704,2 704,300 0,312" fill="url(#aboutFade)"/>
  <polygon points="0,16 704,2 704,300 0,312" fill="url(#steel)"/>
  <polygon points="0,16 704,2 704,300 0,312" fill="url(#sheet)"/>
  <polygon points="0,16 704,2 704,300 0,312" fill="url(#spark)"/>
  <polygon points="0,12 180,14 0,28" fill="#cfdeed"/>
  <polygon points="480,290 704,276 704,316" fill="#0d3a78"/>
  <path d="M0,312 C220,300 460,290 704,318 L704,320 L0,320 Z" fill="#ffffff"/>
</svg>
<h2 class="abs about-title">About<br>Bramblecrest Finishing</h2>
<p class="abs about-text">Ceraflex is a spray on ceramic based finish that can be applied to metals, plastics, polymers and wood. The unique formulation used for Ceraflex ceramic coating enhances a number of physical performance properties including abrasion/wear resistance, corrosion resistance, chemical resistance, impact strength, and hardness.</p>
<a class="abs btn about-btn">Read more</a>

<h2 class="abs contact-title">Contact us</h2>
<div class="abs contact-line" style="top:974px">
  <svg width="21" height="21" viewBox="0 0 24 24"><circle cx="12" cy="12" r="12" fill="#0255a3"/><path fill="#fff" transform="translate(6 6) scale(.5)" d="M6.6 10.8a15 15 0 0 0 6.6 6.6l2.2-2.2a1 1 0 0 1 1-.25 11.4 11.4 0 0 0 3.6.57 1 1 0 0 1 1 1V20a1 1 0 0 1-1 1A17 17 0 0 1 3 4a1 1 0 0 1 1-1h3.5a1 1 0 0 1 1 1c0 1.25.2 2.45.57 3.57a1 1 0 0 1-.25 1z"/></svg>
  <span>555.214.0388</span>
</div>
<div class="abs contact-line" style="top:1009px">
  <svg width="21" height="21" viewBox="0 0 24 24"><circle cx="12" cy="12" r="12" fill="#0255a3"/><path fill="#fff" d="M12 5a4.5 4.5 0 0 0-4.5 4.5C7.5 13 12 18 12 18s4.5-5 4.5-8.5A4.5 4.5 0 0 0 12 5zm0 6.2a1.7 1.7 0 1 1 0-3.4 1.7 1.7 0 0 1 0 3.4z"/></svg>
  <span>418 N Alder Way #6,<br>Fenwick, OR 97412</span>
</div>

<div class="abs field" style="left:270px;top:929px;width:152px;height:21px">Name</div>
<div class="abs field" style="left:429px;top:929px;width:153px;height:21px">Email</div>
<div class="abs field" style="left:270px;top:955px;width:152px;height:21px">Phone</div>
<div class="abs field" style="left:429px;top:955px;width:153px;height:21px">City</div>
<div class="abs field area" style="left:270px;top:982px;width:312px;height:63px">Message</div>
<a class="abs btn submit-btn">Submit</a>

<footer class="abs site-footer"></footer>
<nav class="abs footer-nav"><span>Home</span><span>Coating</span><span>Laser Engraving</span><span>Laser Cutting</span><span>Part Marking</span><span>Contact Us</span></nav>
<p class="abs copyright">© 2018 Company Name &nbsp;All right reserved</p>
<div class="abs social" aria-label="Social links"><span></span><span></span><span></span><span></span></div>

</body>
</html>
```